Verpackungsdesign für Wellness- und Saunaprodukte
Zielgruppe
BaFinn ist ein junges Start-Up, das sich auf Wellness- und Saunaprodukte spezialisiert hat. Unsere Zielgruppe besteht zu beinahe gleichen Teilen aus männlichen und weiblichen Personen zwischen 30 und 60 Jahren. Unsere Produkte befinden sich eher im mittel- bis höherpreisigen Segment, daher streben wir ein hochwertiges Design für unsere Verpackungen an. Unsere Produktpalette reicht von Mentholkristallen, Saunaaufgüssen, bis hin zu Textilien für den Wellnessbereich und soll dementsprechend Menschen ansprechen, die sich einen gewissen Luxus im Alltag auch gönnen.
Aufgabenstellung
Inspiriert von der skandinavischen Sauna Kultur, möchten wir Momente der Erholung und
Entspannung in den Alltag unserer Kunden bringen. Die Geschichte des Saunierens ist eng mit der skandinavischen Kultur verbunden und skandinavische Stilelemente sind zeitgemäß und sprechen ein breites Publikum an. Das Design muss auf Dosen/Tiegel , Karton Verpackungen und Flaschen verschiedener Größen adaptierbar sein (siehe Bild im Anhang).
40g Tiegel(transparent) Höhe 40mm Durchmesser 60mm (ohne Deckel Silber gebürstet)
100g Tiegel(transparent) Höhe 53mm Durchmesser 71mm (ohne Deckel Silber gebürstet)
200g Tiegel(transparent) Höhe 65mm Durchmesser 90mm (ohne Deckel Silber gebürstet)
Karton Verpackung 124,5x49x49mm
Karton Verpackung 100x100x100mm
Flaschenetikett 134x67mm (Braunglas, schwarzer Deckel)
Es soll ein passendes Keyvisual erstellt werden.
Im Anhang sieht man die Verpackungen, Dosen, Flaschen sowie unsere ersten Design Entwürfe (an diese Anordnung der Elemente kann sich der Designer orientieren ). Das Logo bleibt wie gegeben. Das Produkt für die Tiegel soll Mentholkristalle sein.

```html
<!DOCTYPE html>
<html lang="de">
<head>
<meta charset="utf-8">
<title>BaFinn – Verpackungsdesign</title>
<link rel="stylesheet" href="https://fonts.googleapis.com/css2?family=Cormorant+Garamond:wght@600&family=Fira+Sans+Extra+Condensed:wght@300;400;500&display=swap">
<style>
  :root{
    --bg:#efefee;
    --white:#ffffff;
    --band-grey:#d6d8d6;
    --teal:#4a7e73;
    --teal-light:#a4c9c2;
    --teal-tint:#dbeae7;
    --berry:#a55fa4;
    --berry-light:#d0a3cf;
    --berry-tint:#f0e0ef;
    --ink:#2b2b2b;
    --rule:#9a9a9a;
    --ornament:#ececec;
  }
  *{box-sizing:border-box;margin:0;padding:0}
  html,body{width:980px;height:1200px;overflow:hidden;background:var(--bg)}
  body{position:relative;font-family:"Fira Sans Extra Condensed",sans-serif;color:var(--ink)}

  /* ---------- shared label pieces ---------- */
  .label{position:absolute;background:var(--white)}
  .band-top{position:absolute;left:0;right:0;top:0;background:var(--band-grey)}
  .band-bottom{position:absolute;left:0;right:0;bottom:0;background:var(--accent-light)}
  .brand-block{position:absolute;left:50%;transform:translateX(-50%);background:var(--accent);display:flex;align-items:flex-end;justify-content:center;color:#e4ecea;font-family:"Fira Sans Extra Condensed",sans-serif;font-weight:400;letter-spacing:.02em}
  .tag{position:absolute;left:50%;transform:translateX(-50%);bottom:0;background:var(--accent);color:#fff;font-weight:500;display:flex;align-items:center;justify-content:center;letter-spacing:.05em;text-transform:uppercase;white-space:nowrap}
  .mark-field{position:absolute;left:50%;transform:translateX(-50%);background:var(--accent-tint)}
  .col{position:absolute;text-align:center;font-weight:300}
  .col h3{font-family:"Cormorant Garamond",serif;font-weight:600;letter-spacing:.22em;color:var(--ink)}
  .col p{line-height:1.42}
  .title{position:absolute;left:0;right:0;text-align:center;font-family:"Cormorant Garamond",serif;font-weight:600;letter-spacing:.14em;line-height:1;white-space:nowrap}
  .rule{position:absolute;left:50%;transform:translateX(-50%);height:1.5px;background:linear-gradient(90deg,transparent,var(--rule) 20%,var(--rule) 80%,transparent)}
  .subtitle{position:absolute;left:0;right:0;text-align:center;letter-spacing:.3em;font-weight:400;white-space:nowrap}
  .qty{position:absolute;color:#fff;text-align:center;font-weight:300;white-space:nowrap}
  .web{position:absolute;display:flex;align-items:center;color:#fff;letter-spacing:.1em;white-space:nowrap}
  .web .dot{border:1px solid #fff;border-radius:50%;display:inline-block}

  .teal{--accent:var(--teal);--accent-light:var(--teal-light);--accent-tint:var(--teal-tint)}
  .berry{--accent:var(--berry);--accent-light:var(--berry-light);--accent-tint:var(--berry-tint)}

  /* ---------- bottle label ---------- */
  .bottle-label{left:104px;top:388px;width:493px;height:246px}
  .bottle-label .band-top{height:28px}
  .bottle-label .band-bottom{height:28px}
  .bottle-label .brand-block{top:0;width:72px;height:57px;font-size:12px;padding-bottom:8px}
  .bottle-label .mark-field{top:80px;width:42px;height:42px}
  .bottle-label .col{top:47px;width:104px}
  .bottle-label .col h3{font-size:8.5px;margin-bottom:9px;letter-spacing:.2em}
  .bottle-label .col p{font-size:6.6px}
  .bottle-label .col p + p{margin-top:10px}
  .bottle-label .col-left{left:42px}
  .bottle-label .col-right{left:351px}
  .bottle-label .col-right p + p{margin-top:21px}
  .bottle-label .title{top:148px;font-size:17px}
  .bottle-label .rule{top:191px;width:74px}
  .bottle-label .subtitle{top:198px;font-size:10px}
  .bottle-label .tag{width:72px;height:28px;font-size:9.5px}
  .bottle-label .qty{left:55px;width:78px;bottom:5px;font-size:16px}
  .bottle-label .web{left:369px;bottom:9px;font-size:6px;gap:6px}
  .bottle-label .web .dot{width:11px;height:11px}

  /* ---------- carton front ---------- */
  .carton{left:669px;top:152px;width:140px;height:386px}
  .carton .band-top{height:28px}
  .carton .band-bottom{height:28px}
  .carton .brand-block{top:0;width:74px;height:75px;font-size:12px;padding-bottom:14px}
  .carton .mark-field{top:120px;width:46px;height:46px}
  .carton .title{top:208px;font-size:17px}
  .carton .rule{top:250px;width:76px}
  .carton .subtitle{top:257px;font-size:10px}
  .carton .tag{width:74px;height:28px;font-size:9.5px}

  /* ---------- jar labels ---------- */
  .jar-label{top:871px;width:365px;height:127px}
  .jar-left{left:104px}
  .jar-right{left:528px}
  .jar-label .band-top{height:19px}
  .jar-label .band-bottom{height:18px}
  .jar-label .brand-block{top:-33px;width:47px;height:70px;font-size:7px;padding-bottom:8px}
  .jar-label .mark-field{top:52px;width:26px;height:26px}
  .jar-label .col{top:34px;width:76px}
  .jar-label .col h3{font-size:5.5px;margin-bottom:5px;letter-spacing:.18em}
  .jar-label .col p{font-size:4.3px;line-height:1.35}
  .jar-label .col-left{left:26px}
  .jar-label .col-right{left:267px}
  .jar-label .col-right p + p{margin-top:5px}
  .jar-label .divider{display:block;width:48px;height:10px;margin:6px auto}
  .jar-label .title{font-size:10px;letter-spacing:.12em}
  .jar-label .subtitle{font-size:5px;letter-spacing:.1em}
  .jar-label .tag{width:47px;height:18px;font-size:5.5px}
  .jar-label .qty{left:50px;width:30px;bottom:2px;font-size:10px}
  .jar-label .web{left:281px;bottom:5px;font-size:3.8px;gap:4px}
  .jar-label .web .dot{width:7px;height:7px}
</style>
</head>
<body>

<!-- Bottle label -->
<section class="label bottle-label teal" aria-label="Flaschenetikett Nordische Fichte">
  <div class="band-top"></div>
  <div class="brand-block">BaFinn</div>

  <div class="col col-left">
    <h3>INHALTSSTOFFE</h3>
    <p>Lorem ipsum dolor sit amet, consectetuer adipiscing elit, sed diam nonummy nibh euismod tincidunt ut laoreet dolore magna aliquam erat volutpat. Ut wisi enim ad</p>
    <p>Lorem ipsum dolor sit amet, consectetuer adipiscing elit, sed diam nonummy nibh euismod tincidunt ut laoreet dolore magna aliquam erat volutpat. Ut wisi enim ad</p>
  </div>

  <div class="mark-field" role="img" aria-label="Fläche für das Markenzeichen"></div>

  <div class="title">NORDISCHE<br>FICHTE</div>
  <div class="rule"></div>
  <div class="subtitle">AUFGUSS</div>

  <div class="col col-right">
    <h3>ANWENDUNG</h3>
    <p>Lorem ipsum dolor sit amet, consectetuer adipiscing elit, sed diam nonummy nibh euismod tincidunt ut laoreet dolore magna aliquam erat volutpat. Ut wisi enim ad</p>
    <p>Lorem ipsum dolor sit amet, consectetuer adipiscing elit, sed diam nonummy nibh euismod tincidunt ut laoreet dolore magna aliquam erat volutpat. Ut wisi enim ad</p>
  </div>

  <div class="band-bottom"></div>
  <div class="qty">250 ml</div>
  <div class="tag">Für die Sauna</div>
  <div class="web">www.bafinn.de <span class="dot"></span></div>
</section>

<!-- Carton front -->
<section class="label carton teal" aria-label="Kartonverpackung Nordische Fichte">
  <div class="band-top"></div>
  <div class="brand-block">BaFinn</div>
  <div class="mark-field" role="img" aria-label="Fläche für das Markenzeichen"></div>
  <div class="title">NORDISCHE<br>FICHTE</div>
  <div class="rule"></div>
  <div class="subtitle">AUFGUSS</div>
  <div class="band-bottom"></div>
  <div class="tag">Für die Sauna</div>
</section>

<!-- Jar label: Mentholkristalle -->
<section class="label jar-label jar-left teal" aria-label="Tiegeletikett Mentholkristalle">
  <div class="band-top"></div>
  <div class="brand-block">BaFinn</div>
  <div class="col col-left">
    <h3>INHALTSSTOFFE</h3>
    <p>Mentholkristalle aus natürlicher Minze, fein gemahlen und sorgfältig abgefüllt für ein frisches, klares Saunaerlebnis zu Hause</p>
    <svg class="divider" viewBox="0 0 48 10" role="img" aria-label="Zierornament"><rect width="48" height="10" rx="5" fill="var(--ornament)"/></svg>
    <p>Kühl, trocken und gut verschlossen lagern</p>
  </div>
  <div class="mark-field" role="img" aria-label="Fläche für das Markenzeichen"></div>
  <div class="title" style="top:90px">MENTHOLKRISTALLE</div>
  <div class="col col-right">
    <h3>ANWENDUNG</h3>
    <p>Einige Kristalle in das Aufgusswasser geben, kurz lösen lassen und langsam über die heißen Steine gießen</p>
    <p>Nicht direkt auf die Haut auftragen. Außerhalb der Reichweite von Kindern aufbewahren</p>
  </div>
  <div class="band-bottom"></div>
  <div class="qty">40 g</div>
  <div class="tag">Für die Sauna</div>
  <div class="web">www.bafinn.de <span class="dot"></span></div>
</section>

<!-- Jar label: Granatapfel -->
<section class="label jar-label jar-right berry" aria-label="Tiegeletikett Granatapfel Meersalzpeeling">
  <div class="band-top"></div>
  <div class="brand-block">BaFinn</div>
  <div class="col col-left">
    <h3>INHALTSSTOFFE</h3>
    <p>Feines Meersalz mit Granatapfelöl und pflegenden Pflanzenölen, sanft abgestimmt für eine weiche, gepflegte und strahlende Haut</p>
    <svg class="divider" viewBox="0 0 48 10" role="img" aria-label="Zierornament"><rect width="48" height="10" rx="5" fill="var(--ornament)"/></svg>
    <p>Kühl, trocken und gut verschlossen lagern</p>
  </div>
  <div class="mark-field" role="img" aria-label="Fläche für das Markenzeichen"></div>
  <div class="title" style="top:86px">GRANATAPFEL</div>
  <div class="subtitle" style="top:99px">MEERSALZPEELING</div>
  <div class="col col-right">
    <h3>ANWENDUNG</h3>
    <p>Eine kleine Menge auf die feuchte Haut geben, in kreisenden Bewegungen massieren und gründlich abspülen</p>
    <p>Nicht auf gereizter Haut anwenden. Außerhalb der Reichweite von Kindern aufbewahren</p>
  </div>
  <div class="band-bottom"></div>
  <div class="qty">40 g</div>
  <div class="tag">Für den Körper</div>
  <div class="web">www.bafinn.de <span class="dot"></span></div>
</section>

</body>
</html>
```